Coastline Premier Retreats Business Card Design

Design a business card for Coastline Premier Retreats. Look at the website for colors and reference. Card should have logo, name, title, office number, mobile number, email, URL and a tagline like, "Luxury Hotel & Resort Email Marketing" (This might change).

https://www.coastlinepremierretreats.example

The rest I will leave up to your imagination.

Contact Information for Business Card

Logo, name, title, office number, mobile number, email, URL and a tagline like, "Luxury Hotel & Resort Email Marketing" (This might change).

```html
<!DOCTYPE html>
<html lang="en">
<head>
<meta charset="UTF-8">
<title>Coastline Premier Retreats — Business Card</title>
<link rel="stylesheet" href="https://fonts.googleapis.com/css2?family=Open+Sans:wght@400;600;700&display=swap">
<style>
  :root {
    --stage: #232323;
    --orange: #f37421;
    --ink: #1f1f22;
    --white: #ffffff;
    --card-w: 340px;
    --card-h: 560px;
    --curve: 130px;
  }
  * { box-sizing: border-box; margin: 0; padding: 0; }
  html, body {
    width: 1200px; height: 780px; overflow: hidden;
    background: var(--stage);
    font-family: "Open Sans", Arial, sans-serif;
  }
  .stage {
    width: 1200px; height: 780px;
    display: flex; align-items: center; justify-content: center; gap: 80px;
  }
  .card {
    width: var(--card-w); height: var(--card-h);
    position: relative; overflow: hidden;
    box-shadow: 0 18px 40px rgba(0,0,0,.45);
  }
  /* Front */
  .card--front {
    background: var(--orange);
    border-radius: var(--curve) 0 var(--curve) 0;
  }
  .front-brand {
    position: absolute; left: 50%; top: 50%;
    transform: translate(-50%, -50%) rotate(-90deg);
    white-space: nowrap; text-align: center;
    color: var(--white); font-weight: 700;
  }
  .front-brand__name {
    font-size: 40px; letter-spacing: 2px; text-transform: uppercase; line-height: 1.1;
  }
  /* Back */
  .card--back {
    background: var(--ink);
    border: 1.5px solid var(--orange);
    border-radius: 0 var(--curve) 0 var(--curve);
    padding: 46px 34px 0 34px;
  }
  .back-brand {
    color: var(--white); font-weight: 700; font-size: 19px;
    letter-spacing: 1.5px; text-transform: uppercase; text-align: center;
    line-height: 1.2;
  }
  .person { position: absolute; left: 34px; right: 24px; top: 300px; }
  .person__name { font-size: 30px; font-weight: 700; color: var(--white); line-height: 1.1; }
  .person__name .first { color: var(--orange); }
  .person__title { font-size: 14px; font-weight: 600; color: var(--white); margin-top: 4px; }
  .person__tagline { font-size: 13px; color: var(--orange); margin-top: 16px; line-height: 1.35; }
  .contact { list-style: none; margin-top: 18px; }
  .contact__item {
    display: flex; align-items: center; gap: 9px;
    font-size: 12px; color: var(--white); line-height: 1.9;
  }
  .contact__icon { width: 13px; height: 13px; flex: none; }
</style>
</head>
<body>
<main class="stage">
  <section class="card card--front" aria-label="Card front">
    <div class="front-brand">
      <div class="front-brand__name">Coastline Premier<br>Retreats</div>
    </div>
  </section>

  <section class="card card--back" aria-label="Card back">
    <div class="back-brand">Coastline Premier<br>Retreats</div>
    <div class="person">
      <h1 class="person__name"><span class="first">Helena</span> Varga</h1>
      <p class="person__title">Co-Founder</p>
      <p class="person__tagline">Luxury Hotel &amp;<br>Resort Email Marketing</p>
      <ul class="contact">
        <li class="contact__item">
          <svg class="contact__icon" viewBox="0 0 16 16"><path fill="#f37421" d="M3.5 1.5l2.5 0 1 3.5-1.6 1.2a8 8 0 0 0 4.4 4.4L11 9l3.5 1v2.5a2 2 0 0 1-2 2A11 11 0 0 1 1.5 3.5a2 2 0 0 1 2-2z"/></svg>
          (555) 014-2758
        </li>
        <li class="contact__item">
          <svg class="contact__icon" viewBox="0 0 16 16"><rect x="4" y="1" width="8" height="14" rx="1.5" fill="none" stroke="#fff" stroke-width="1.3"/></svg>
          (555) 019-7777
        </li>
        <li class="contact__item">
          <svg class="contact__icon" viewBox="0 0 16 16"><circle cx="8" cy="8" r="6.5" fill="none" stroke="#f37421" stroke-width="1.4"/><path d="M1.5 8h13M8 1.5c-3 3-3 10 0 13M8 1.5c3 3 3 10 0 13" fill="none" stroke="#f37421" stroke-width="1.1"/></svg>
          www.coastlinepremierretreats.example
        </li>
        <li class="contact__item">
          <svg class="contact__icon" viewBox="0 0 16 16"><rect x="1" y="3" width="14" height="10" rx="1" fill="#f37421"/><path d="M1.5 3.5L8 9l6.5-5.5" fill="none" stroke="#1f1f22" stroke-width="1.2"/></svg>
          info@coastlinepremierretreats.example
        </li>
      </ul>
    </div>
  </section>
</main>
</body>
</html>
```